Stonebridge Building and Projects business cards

A business card with watermark background (construction work)

Company logo attached

Home improvement projects
House renovations
Bathroom and kitchen renovations
House extensions
New builds and granny flats

Director Omar Haddani
(Phone number)
omar@sbpbuilding.com.au
(Instagram logo) sbp_building

```html
<!DOCTYPE html>
<html lang="en">
<head>
<meta charset="utf-8">
<title>Stonebridge Building and Projects – Business Cards</title>
<link href="https://fonts.googleapis.com/css2?family=Montserrat:wght@500;600;700&family=Roboto:wght@400;500&display=swap" rel="stylesheet">
<style>
  :root{
    --bg:#2a2a2b;
    --card:#121314;
    --card-edge:#1c1d1f;
    --blue:#1a86d0;
    --white:#f2f4f6;
    --grey:#b9bcc0;
    --silver:#8e9196;
    --shadow-band:#6b6e72;
  }
  *{box-sizing:border-box;margin:0;padding:0}
  html,body{width:1200px;height:1050px;overflow:hidden;background:var(--bg)}
  body{font-family:"Roboto",Arial,sans-serif;color:var(--white);display:flex;flex-direction:column;align-items:center;justify-content:center;gap:30px}
  .card{position:relative;width:840px;height:480px;border-radius:26px;background:linear-gradient(135deg,var(--card-edge),var(--card));overflow:hidden}

  /* front */
  .watermark{position:absolute;right:0;top:0;width:520px;height:380px;background:radial-gradient(ellipse at 60% 40%,rgba(255,255,255,.07),rgba(255,255,255,0) 70%)}
  .logo-word{position:absolute;font-family:"Montserrat",sans-serif;font-weight:700;color:var(--blue);letter-spacing:1px}
  .front .logo-word{left:60px;top:120px;font-size:44px}
  .company{position:absolute;left:390px;top:60px;font-family:"Montserrat",sans-serif}
  .company .line1{font-size:38px;font-weight:600;color:var(--white);line-height:1.1}
  .company .line2{font-size:15px;font-weight:500;letter-spacing:6px;color:var(--white);text-transform:uppercase;margin-top:6px;border-top:2px solid var(--blue);border-bottom:2px solid var(--blue);padding:4px 0;display:inline-block}
  .company .tagline{font-size:22px;font-weight:600;color:var(--blue);margin-top:8px}
  .person{position:absolute;left:60px;top:290px}
  .person .name{font-family:"Montserrat",sans-serif;font-weight:700;font-size:30px;color:var(--blue)}
  .person .role{font-size:18px;color:var(--white);margin-top:4px}
  .person .licence{font-size:18px;color:var(--white);margin-top:46px}
  .contacts{position:absolute;left:400px;top:240px;list-style:none;font-size:19px;color:var(--white)}
  .contacts li{display:flex;align-items:center;gap:14px;height:32px}
  .contacts svg{width:18px;height:18px;flex:none}
  .band-shadow{position:absolute;left:0;bottom:0;width:100%;height:70px;background:var(--shadow-band)}
  .band-blue{position:absolute;right:0;bottom:0;width:460px;height:92px;background:var(--blue);border-top-left-radius:40px;display:flex;align-items:center;gap:14px;padding-left:50px;font-size:20px}
  .front .band-shadow{width:400px;height:18px}
  .ring{width:18px;height:18px;border:2px solid var(--white);border-radius:50%}

  /* back */
  .back .logo-word{left:0;right:0;top:95px;text-align:center;font-size:110px;color:var(--silver)}
  .services{position:absolute;left:0;top:250px;width:100%;height:120px;background:var(--blue);display:flex;flex-direction:column;justify-content:center;align-items:center;gap:8px;font-size:21px;color:var(--white)}
  .back-links{position:absolute;left:0;right:0;top:400px;display:flex;justify-content:center;gap:60px;font-size:20px}
  .back-links span{display:flex;align-items:center;gap:12px}
</style>
</head>
<body>
  <section class="card front">
    <div class="watermark" role="img" aria-label="Faint background photo of construction work"></div>
    <div class="logo-word">Stonebridge</div>
    <div class="company">
      <div class="line1">Stonebridge Building</div>
      <div class="line2">and Projects</div>
      <div class="tagline">Built to last!</div>
    </div>
    <div class="person">
      <div class="name">Omar Haddani</div>
      <div class="role">Managing Director</div>
      <div class="licence">Lic. no.: 481207C</div>
    </div>
    <ul class="contacts">
      <li><svg viewBox="0 0 24 24" fill="none" stroke="var(--blue)" stroke-width="2"><path d="M5 3h4l2 5-3 2a12 12 0 0 0 6 6l2-3 5 2v4a2 2 0 0 1-2 2A18 18 0 0 1 3 5a2 2 0 0 1 2-2z"/></svg>0400 123 987</li>
      <li><svg viewBox="0 0 24 24" fill="none" stroke="var(--blue)" stroke-width="2"><rect x="3" y="5" width="18" height="14" rx="2"/><path d="M3 7l9 6 9-6"/></svg>omar@sbpbuilding.com.au</li>
      <li><svg viewBox="0 0 24 24" fill="none" stroke="var(--blue)" stroke-width="2"><circle cx="12" cy="12" r="9"/><path d="M3 12h18M12 3c3 3 3 15 0 18M12 3c-3 3-3 15 0 18"/></svg>www.sbpbuilding.com.au</li>
    </ul>
    <div class="band-shadow"></div>
    <div class="band-blue"><span class="ring"></span>sbp_building</div>
  </section>

  <section class="card back">
    <div class="logo-word">Stonebridge</div>
    <div class="services">
      <div>Home Improvement Projects &nbsp;|&nbsp; House Renovations &nbsp;|&nbsp; House Extensions</div>
      <div>Bathroom &amp; Kitchen Renovations &nbsp;|&nbsp; New Builds &amp; Granny Flats</div>
    </div>
    <div class="back-links">
      <span><span class="ring" style="border-color:var(--blue)"></span>sbp_building</span>
      <span><svg width="20" height="20" viewBox="0 0 24 24" fill="none" stroke="var(--blue)" stroke-width="2"><circle cx="12" cy="12" r="9"/><path d="M3 12h18M12 3c3 3 3 15 0 18M12 3c-3 3-3 15 0 18"/></svg>sbpbuilding.com.au</span>
    </div>
  </section>
</body>
</html>
```